Business card for Luxury Portable Restroom Trailer company

We are a Luxury Portable Restroom Trailer Company Called FALCRIDGE HIRES. Based in Orange County California. We provide portable restroom trailers for events, such as, Weddings, Concerts, Charity events, Sporting events, Tournaments, Corporate events, ect. We rent and Sell the Luxury restrooms. Our colors are white, grey, and Orange. As you will see in the logo we uploaded.
There are 2 people in the company so the names and titles will change for the 3 people but card will remain the same. Here is the information for each Person: Dwight Penner CFO 555 318-0476
next Person: Leon Marchetti VP 555 318-0476
Next Person: Owen Marchetti CEO 555 318-0476
Information to include on the card: Luxury Restroom Trailers Rental and Sales. Weddings, Concerts, Charity, Sporting and Corp. Events.

```html
<!DOCTYPE html>
<html lang="en">
<head>
<meta charset="utf-8">
<title>Falcridge Hires – Business Card</title>
<link rel="stylesheet" href="https://fonts.googleapis.com/css2?family=Montserrat:wght@400;500;700;800&display=swap">
<style>
  :root {
    --orange: #f06a25;
    --peach: #fde9dd;
    --grey: #4a4a4c;
    --ink: #222226;
    --white: #ffffff;
    --backdrop: #e7e7e9;
  }
  * { margin: 0; padding: 0; box-sizing: border-box; }
  html, body { width: 1200px; height: 900px; overflow: hidden; }
  body {
    background: var(--backdrop);
    font-family: "Montserrat", Arial, sans-serif;
    position: relative;
  }
  .card {
    position: absolute;
    left: 250px;
    width: 700px;
    height: 400px;
    background: var(--white);
    border-radius: 22px;
    overflow: hidden;
    box-shadow: 0 6px 18px rgba(0,0,0,0.12);
  }
  .card--front { top: 30px; }
  .card--back { top: 470px; }

  /* front */
  .front-decoration { position: absolute; inset: 0; }
  .front-logo {
    position: absolute;
    left: 0; right: 0; top: 110px;
    text-align: center;
    color: var(--orange);
    font-weight: 800;
    line-height: 1;
  }
  .front-logo .word-main { display: block; font-size: 78px; letter-spacing: 2px; }
  .front-logo .word-sub { display: block; font-size: 38px; letter-spacing: 10px; margin-top: 10px; }
  .front-tagline {
    position: absolute;
    left: 0; right: 0; top: 282px;
    text-align: center;
    color: var(--grey);
    font-size: 15px;
    font-weight: 500;
    line-height: 1.55;
  }
  .front-tagline .tagline-main { display: block; font-weight: 700; font-size: 17px; color: var(--ink); }

  /* back */
  .back-panel { position: absolute; inset: 0; }
  .back-logo {
    position: absolute;
    left: 46px; top: 40px;
    color: var(--orange);
    font-weight: 800;
    line-height: 1;
  }
  .back-logo .word-main { display: block; font-size: 30px; letter-spacing: 1px; }
  .back-logo .word-sub { display: block; font-size: 15px; letter-spacing: 5px; margin-top: 4px; }

  .person { position: absolute; left: 46px; top: 128px; }
  .person-name { color: var(--orange); font-weight: 700; font-size: 26px; }
  .person-title { color: var(--ink); font-size: 14px; font-weight: 500; margin-top: 2px; }

  .address {
    position: absolute; left: 46px; top: 200px;
    color: var(--ink); font-size: 14px; line-height: 1.4; font-style: normal;
  }
  .contact-list {
    position: absolute; left: 46px; top: 256px;
    list-style: none; color: var(--ink); font-size: 14px;
  }
  .contact-list li { display: flex; align-items: center; gap: 10px; height: 24px; }
  .contact-list svg { width: 14px; height: 14px; fill: var(--orange); flex: none; }

  .back-services {
    position: absolute; right: 30px; bottom: 30px;
    width: 220px;
    color: var(--white);
    font-size: 13px;
    font-weight: 500;
    line-height: 1.45;
    text-align: right;
  }
  .back-services .services-main { display: block; font-weight: 700; font-size: 14px; margin-bottom: 4px; }
</style>
</head>
<body>

<section class="card card--front" aria-label="Card front">
  <svg class="front-decoration" viewBox="0 0 700 400" role="img" aria-label="Faint brand emblem area in pale peach">
    <path d="M300 0 L700 0 L700 400 L120 400 Z" fill="var(--peach)"/>
  </svg>
  <div class="front-logo">
    <span class="word-main">FALCRIDGE</span>
    <span class="word-sub">HIRES</span>
  </div>
  <p class="front-tagline">
    <span class="tagline-main">Luxury Restroom Trailers Rental and Sales</span>
    Weddings, Concerts, Charity, Sporting and Corp. Events
  </p>
</section>

<section class="card card--back" aria-label="Card back">
  <svg class="back-panel" viewBox="0 0 700 400" role="img" aria-label="Large brand emblem area in orange">
    <path d="M540 0 L700 0 L700 400 L400 400 Z" fill="var(--orange)"/>
  </svg>

  <div class="back-logo">
    <span class="word-main">FALCRIDGE</span>
    <span class="word-sub">HIRES</span>
  </div>

  <div class="person">
    <div class="person-name">Owen Marchetti</div>
    <div class="person-title">CEO</div>
  </div>

  <address class="address">
    418 Harbor Crest Ave, #112<br>
    Tustin, CA 92780
  </address>

  <ul class="contact-list">
    <li>
      <svg viewBox="0 0 24 24" aria-hidden="true"><path d="M6.6 10.8a15 15 0 0 0 6.6 6.6l2.2-2.2c.3-.3.7-.4 1-.2 1.1.4 2.3.6 3.6.6.6 0 1 .4 1 1V20c0 .6-.4 1-1 1A17 17 0 0 1 3 4c0-.6.4-1 1-1h3.5c.6 0 1 .4 1 1 0 1.3.2 2.5.6 3.6.1.3 0 .7-.2 1z"/></svg>
      555 318-0476
    </li>
    <li>
      <svg viewBox="0 0 24 24" aria-hidden="true"><path d="M7 1h10a2 2 0 0 1 2 2v18a2 2 0 0 1-2 2H7a2 2 0 0 1-2-2V3a2 2 0 0 1 2-2zm0 3v14h10V4zm5 15.5a1 1 0 1 0 0 2 1 1 0 0 0 0-2z"/></svg>
      555 318-0476
    </li>
    <li>
      <svg viewBox="0 0 24 24" aria-hidden="true"><path d="M2 5h20v14H2zm2 2v.5l8 5 8-5V7zm0 2.8V17h16V9.8l-8 5z"/></svg>
      info@falcridgehires.com
    </li>
    <li>
      <svg viewBox="0 0 24 24" aria-hidden="true"><path d="M12 2a10 10 0 1 0 0 20 10 10 0 0 0 0-20zm6.9 6h-3a15 15 0 0 0-1.3-3.9A8 8 0 0 1 18.9 8zM12 4c.8 1.2 1.5 2.5 1.9 4h-3.8c.4-1.5 1.1-2.8 1.9-4zM4.3 14a8 8 0 0 1 0-4h3.4a16 16 0 0 0 0 4zm.8 2h3a15 15 0 0 0 1.3 3.9A8 8 0 0 1 5.1 16zm3-8h-3a8 8 0 0 1 4.3-3.9C8.8 5.3 8.4 6.6 8.1 8zM12 20c-.8-1.2-1.5-2.5-1.9-4h3.8c-.4 1.5-1.1 2.8-1.9 4zm2.3-6H9.7a14 14 0 0 1 0-4h4.6a14 14 0 0 1 0 4zm.3 5.9c.6-1.2 1-2.5 1.3-3.9h3a8 8 0 0 1-4.3 3.9zm1.7-5.9a16 16 0 0 0 0-4h3.4a8 8 0 0 1 0 4z"/></svg>
      www.falcridgehires.com
    </li>
  </ul>

  <p class="back-services">
    <span class="services-main">Luxury Restroom Trailers<br>Rental and Sales</span>
    Weddings, Concerts, Charity,<br>Sporting and Corp. Events
  </p>
</section>

</body>
</html>
```